Construction business card

I need a new business card, they can connect with my logo, brand.
What we do is residential house , design and build
I like: Navy blue / black
I attached our logo, brand,
and, some idea for business card.

```html
<!DOCTYPE html>
<html lang="en">
<head>
<meta charset="utf-8">
<title>Norvale Building Group – Business Card</title>
<link rel="stylesheet" href="https://fonts.googleapis.com/css2?family=Arimo:wght@400;700&display=swap">
<style>
  :root {
    --page: #161617;
    --card: #29292b;
    --mark-deep: #1d1d1f;
    --accent: #2f80cc;
    --text: #f2f2f2;
  }
  * { box-sizing: border-box; margin: 0; padding: 0; }
  html, body { width: 1200px; height: 900px; overflow: hidden; }
  body {
    background: var(--page);
    font-family: "Arimo", Arial, sans-serif;
    display: flex;
    flex-direction: column;
    align-items: center;
    justify-content: center;
    gap: 50px;
  }
  .card {
    width: 620px;
    height: 354px;
    background: var(--card);
    border-radius: 22px;
    position: relative;
    overflow: hidden;
  }
  /* front */
  .card--front {
    display: flex;
    align-items: center;
    justify-content: center;
  }
  .brand {
    display: flex;
    align-items: center;
    gap: 14px;
  }
  .brand__square {
    width: 26px;
    height: 26px;
    background: var(--mark-deep);
  }
  .brand__name {
    font-weight: 700;
    font-size: 34px;
    color: var(--mark-deep);
    text-transform: uppercase;
    letter-spacing: 1px;
  }
  /* back */
  .card--back .brand-deco {
    position: absolute;
    right: 30px;
    top: 150px;
    font-weight: 700;
    font-size: 56px;
    line-height: 1;
    white-space: nowrap;
    color: var(--mark-deep);
    text-transform: uppercase;
    letter-spacing: -1px;
  }
  .contact {
    position: absolute;
    left: 44px;
    top: 78px;
    width: 250px;
    color: var(--text);
    font-size: 17px;
    line-height: 1.3;
  }
  .contact__name {
    color: var(--accent);
    font-weight: 700;
    font-size: 27px;
    text-transform: uppercase;
    line-height: 1.05;
    white-space: nowrap;
  }
  .contact__title { font-size: 17px; }
  .contact__rule {
    width: 14px;
    height: 2px;
    background: var(--accent);
    margin: 14px 0 10px;
  }
  .contact__list { list-style: none; }
  .contact__list li {
    display: flex;
    align-items: center;
    gap: 10px;
    margin-bottom: 6px;
    white-space: nowrap;
  }
  .contact__list svg { width: 15px; height: 15px; flex: none; }
</style>
</head>
<body>

  <section class="card card--front" aria-label="Card front">
    <div class="brand">
      <span class="brand__square"></span>
      <span class="brand__name">Norvale Building Group</span>
    </div>
  </section>

  <section class="card card--back" aria-label="Card back">
    <div class="brand-deco" aria-hidden="true">Norvale</div>

    <div class="contact">
      <p class="contact__name">Daniel Hart</p>
      <p class="contact__title">CEO/Founder</p>
      <div class="contact__rule"></div>
      <p>42 Carrow St,<br>Eastmere, VIC 3190</p>
      <div class="contact__rule"></div>
      <ul class="contact__list">
        <li>
          <svg viewBox="0 0 16 16" aria-hidden="true"><path fill="var(--accent)" d="M3.5 1.5l2.3 2.9-1.3 1.6c.9 2 2.5 3.6 4.5 4.5l1.6-1.3 2.9 2.3-1.4 2.3C7 13.5 2.5 9 1.2 2.9z"/></svg>
          <span>0400 555 018</span>
        </li>
        <li>
          <svg viewBox="0 0 16 16" aria-hidden="true"><rect x="1" y="3" width="14" height="10" rx="1.5" fill="var(--accent)"/><path d="M1.5 4l6.5 5 6.5-5" stroke="var(--card)" stroke-width="1.4" fill="none"/></svg>
          <span>info@norvalebuild.com.au</span>
        </li>
        <li>
          <svg viewBox="0 0 16 16" aria-hidden="true"><circle cx="8" cy="8" r="7" fill="var(--accent)"/><path d="M1 8h14M8 1c-3 3.5-3 10.5 0 14M8 1c3 3.5 3 10.5 0 14" stroke="var(--card)" stroke-width="1.1" fill="none"/></svg>
          <span>norvalebuild.com.au</span>
        </li>
      </ul>
    </div>
  </section>

</body>
</html>
```